Kestrova - presentation for a remote DBA team offering data platform management

We need a website design for wordpress site called Kestrova.cz
We deliver remote database and data platform administration and development, oversee the database administrators, consult and train the personnel responsible for the database operations. The website should include several sections, home page with graphics elements supporting the name and service - remote dba work; blog section; service introduction and description, team introduction and description, download section for documents, presentations etc.

Target Market(s)

small and medium business companies requiring remote DBA service

Number of Pages Required

3 page

Font styles to use
Sans Serif

Colors

Designer to choose colors to be used in the design.

Requirements
Must have
• The website should have several sections to introduce the services, blog, team introduction, downloads

```html
<!DOCTYPE html>
<html lang="en">
<head>
<meta charset="utf-8">
<title>Kestrova – Data Platform Management</title>
<link href="https://fonts.googleapis.com/css2?family=Poppins:wght@400;500;600;700&family=Open+Sans:wght@400;600;700&display=swap" rel="stylesheet">
<style>
:root{
  --blue:#1160b0;
  --blue-dark:#0d4f96;
  --blue-light:#1a86d8;
  --navy:#0e2440;
  --ink:#222a33;
  --muted:#555d66;
  --soft:#f3f3f4;
  --white:#ffffff;
  --line:#d8dbe0;
}
*{box-sizing:border-box;margin:0;padding:0}
html,body{width:1200px;height:4545px;overflow:hidden}
body{font-family:"Open Sans",Arial,sans-serif;color:var(--ink);background:var(--white);position:relative}
h1,h2,h3,h4,.brand,.btn,.nav a{font-family:"Poppins",Arial,sans-serif}
section,header,footer{position:absolute;left:0;width:1200px}
.abs{position:absolute}
.center{text-align:center}
.divider{position:absolute;left:560px;width:80px;height:2px;background:#9aa0a8}

/* header */
.site-header{top:0;height:85px;background:var(--white)}
.brand{position:absolute;left:133px;top:24px;font-size:31px;font-weight:700;color:var(--blue);letter-spacing:.5px}
.nav{position:absolute;left:398px;top:36px;display:flex;gap:31px}
.nav a{font-size:12.5px;font-weight:600;color:var(--navy);text-decoration:none;letter-spacing:.3px}
.nav a.active{color:var(--blue);border-bottom:2px solid var(--blue);padding-bottom:3px}
.social-top{position:absolute;left:967px;top:31px;display:flex;gap:6px}
.social-top span{width:27px;height:27px;border-radius:50%;display:block}

/* hero */
.hero{top:85px;height:570px}
.hero-photo{position:absolute;inset:0;background:linear-gradient(100deg,#0b1a2c 0%,#173758 35%,#2f5f88 55%,#122b47 80%,#0a1626 100%)}
.hero h1{position:absolute;left:133px;top:170px;font-size:49px;line-height:56px;font-weight:700;color:var(--white);letter-spacing:.5px}
.btn{display:inline-block;background:var(--blue);color:var(--white);font-weight:600;text-align:center;text-decoration:none}
.hero .btn{position:absolute;left:133px;top:309px;width:152px;height:46px;line-height:46px;font-size:16px}
.hero-dots{position:absolute;top:510px;left:536px;display:flex;gap:17px}
.hero-dots span{width:9px;height:9px;border-radius:50%;background:var(--white)}
.hero-dots span.on{background:transparent;border:2px solid var(--white);width:11px;height:11px;margin-top:-1px}

/* welcome */
.welcome{top:655px;height:800px;background:var(--soft)}
.section-title{position:absolute;left:0;width:1200px;text-align:center;font-size:32px;font-weight:600;color:#111}
.welcome-photo{position:absolute;left:133px;top:200px;width:437px;height:430px;background:linear-gradient(135deg,#f2a25a 0%,#d9cdc2 35%,#e7e9ee 60%,#b8bcc5 100%)}
.welcome-text{position:absolute;left:160px;top:655px;width:380px;font-size:18px;line-height:27px;color:#222}
.feature{position:absolute;left:597px;width:466px;height:103px;display:flex}
.feature-icon{width:100px;height:103px;background:var(--blue);display:flex;align-items:center;justify-content:center}
.feature-body{flex:1;background:var(--white);box-shadow:0 2px 8px rgba(0,0,0,.12);padding:28px 0 0 30px}
.feature-body h4{font-size:13.5px;font-weight:700;color:#111;margin-bottom:8px}
.feature-body p{font-size:12.5px;line-height:17px;color:#333}

/* services */
.services{top:1455px;height:690px;background:var(--white)}
.service-card{position:absolute;top:208px;width:294px;height:400px;background:var(--white);box-shadow:0 2px 10px rgba(0,0,0,.16);text-align:center}
.service-card svg{margin-top:42px}
.service-card h3{font-size:18px;font-weight:500;line-height:26px;color:#111;margin-top:22px}
.service-card p{font-size:13px;line-height:18.5px;color:#333;width:230px;margin:14px auto 0}
.service-card .btn{position:absolute;left:97px;top:340px;width:100px;height:27px;line-height:27px;font-size:11px}

/* help */
.help{top:2145px;height:622px;background:var(--blue)}
.help h2{position:absolute;width:1200px;top:75px;text-align:center;color:var(--white);font-size:33px;font-weight:600}
.help .lead{position:absolute;left:380px;width:440px;top:140px;text-align:center;color:#e6eefa;font-size:15px;line-height:22px}
.tile{position:absolute;top:245px;width:293px;height:298px;text-align:center;color:var(--white)}
.tile-photo{position:absolute;inset:0}
.tile-shade{position:absolute;inset:0;background:rgba(10,20,35,.45)}
.tile h3{position:relative;margin-top:113px;font-size:22px;font-weight:700;letter-spacing:.3px}
.tile p{position:relative;width:200px;margin:6px auto 0;font-size:14px;line-height:19px;color:#e9edf3}

/* blog */
.blog{top:2767px;height:642px;background:linear-gradient(180deg,#f7f8f9,#eceef0)}
.post{position:absolute;top:223px;width:257px;height:334px;background:var(--white);box-shadow:0 3px 10px rgba(0,0,0,.18);overflow:hidden}
.post-photo{position:absolute;left:0;top:0;width:257px;height:176px}
.post-cut{position:absolute;left:0;top:150px}
.post h4{position:absolute;left:38px;top:200px;width:200px;font-size:14px;line-height:19px;font-weight:600;color:#111}
.post p{position:absolute;left:38px;top:245px;width:200px;font-size:10.5px;line-height:13px;color:#555}
.post .btn{position:absolute;right:16px;top:297px;width:76px;height:23px;line-height:23px;font-size:11px}
.post-corner{position:absolute;left:0;bottom:0}

/* testimonial */
.testimonial{top:3409px;height:418px;background:var(--white)}
.testimonial h3{position:absolute;width:1200px;top:98px;text-align:center;font-size:21px;font-weight:600;color:#111}
.quote{position:absolute;left:270px;width:660px;top:150px;text-align:center;font-size:25px;line-height:37px;color:#2a3b5a}
.testimonial .by{position:absolute;width:1200px;top:262px;text-align:center;font-size:15px;color:#333}
.t-dots{position:absolute;left:568px;top:328px;display:flex;gap:9px}
.t-dots span{width:9px;height:9px;border-radius:50%;background:#b7bcc4}
.t-dots span.on{background:#2a3b5a}

/* cta */
.cta{top:3827px;height:343px}
.cta-panel{position:absolute;top:0;height:343px;text-align:center;color:var(--white)}
.cta-left{left:0;width:612px;background:var(--blue-dark)}
.cta-right{left:612px;width:588px;background:var(--blue-light)}
.cta-panel h3{margin-top:82px;font-size:27px;font-weight:600}
.cta-panel p{width:320px;margin:18px auto 0;font-size:15px;line-height:20px;color:#eef4fc}
.cta-panel .outline{display:inline-block;margin-top:28px;width:110px;height:30px;line-height:26px;border:2px solid var(--white);color:var(--white);font-family:"Poppins",Arial,sans-serif;font-size:12.5px;font-weight:600}

/* footer */
.site-footer{top:4170px;height:375px;background:#f1f2f3}
.footer-brand{position:absolute;left:180px;top:115px;font-size:31px;font-weight:700;color:var(--blue)}
.footer-col h5{font-family:"Poppins",Arial,sans-serif;font-size:11.5px;font-weight:700;color:var(--blue);margin-bottom:20px;letter-spacing:.3px}
.footer-col{position:absolute;top:64px;font-size:11.5px;color:#222}
.contact-row{display:flex;gap:16px;margin-bottom:22px;line-height:15px}
.contact-row svg{flex:none;margin-top:1px}
.menu-list{list-style:none;line-height:17px;font-size:11.5px}
.connect-row{display:flex;align-items:center;gap:12px;margin-bottom:14px}
.connect-row span{width:27px;height:27px;border-radius:50%;background:var(--blue-dark);display:block}
.footer-line{position:absolute;left:133px;width:934px;top:278px;height:1px;background:#cfd2d6}
.copyright{position:absolute;width:1200px;top:326px;text-align:center;font-size:11px;color:#333}
</style>
</head>
<body>

<header class="site-header">
  <div class="brand">KESTROVA</div>
  <nav class="nav">
    <a class="active" href="#">HOME</a>
    <a href="#">ABOUT US</a>
    <a href="#">SOLUTIONS</a>
    <a href="#">TECHNOLOGIES</a>
    <a href="#">BLOG</a>
    <a href="#">CONTACT US</a>
  </nav>
  <div class="social-top">
    <span style="background:#2b4f9c"></span>
    <span style="background:#1b9ae0"></span>
    <span style="background:#0e2440"></span>
  </div>
</header>

<section class="hero">
  <div class="hero-photo" role="img" aria-label="Engineer with a laptop walking through a lit server room aisle"></div>
  <h1>DATA PLATFORM<br>MANAGEMENT.</h1>
  <a class="btn" href="#">READ MORE</a>
  <div class="hero-dots"><span></span><span></span><span class="on"></span><span></span><span></span></div>
</section>

<section class="welcome">
  <h2 class="section-title" style="top:67px">Welcome to our site</h2>
  <div class="divider" style="top:124px"></div>
  <div class="welcome-photo" role="img" aria-label="Hands typing on a laptop keyboard in warm light"></div>
  <p class="welcome-text">Contrary to popular belief Lorem Ipsum simply random text It has roots in lassical Latin literature.</p>

  <div class="feature" style="top:245px">
    <div class="feature-icon">
      <svg width="50" height="50" viewBox="0 0 50 50" fill="none" stroke="#fff" stroke-width="2.5"><rect x="19" y="4" width="12" height="10" fill="#fff"/><path d="M25 14v9M9 23h32M9 23v7M25 23v7M41 23v7"/><rect x="3" y="30" width="12" height="10" fill="#fff"/><rect x="19" y="30" width="12" height="10" fill="#fff"/><rect x="35" y="30" width="12" height="10" fill="#fff"/></svg>
    </div>
    <div class="feature-body"><h4>STRONG MANAGEMENT</h4><p>Lorem Ipsum is simply dummy text of the printing and typesetting industry.</p></div>
  </div>
  <div class="feature" style="top:357px">
    <div class="feature-icon">
      <svg width="52" height="50" viewBox="0 0 52 50" fill="none" stroke="#fff" stroke-width="2.5"><rect x="18" y="8" width="26" height="16" rx="2" transform="rotate(-25 31 16)"/><circle cx="31" cy="16" r="4"/><path d="M4 40c6-8 12-10 20-6l10 4M4 46h16l16-8"/></svg>
    </div>
    <div class="feature-body"><h4>LOW COST</h4><p>Lorem Ipsum is simply dummy text of the printing and typesetting industry.</p></div>
  </div>
  <div class="feature" style="top:472px">
    <div class="feature-icon">
      <svg width="50" height="50" viewBox="0 0 50 50" fill="none" stroke="#fff" stroke-width="3"><path d="M9 28v-5a16 16 0 0 1 32 0v5"/><rect x="6" y="26" width="8" height="13" rx="3" fill="#fff"/><rect x="36" y="26" width="8" height="13" rx="3" fill="#fff"/><path d="M40 39c0 5-6 7-12 7"/></svg>
    </div>
    <div class="feature-body"><h4>24/7 AVAILABILITY</h4><p>Lorem Ipsum is simply dummy text of the printing and typesetting industry.</p></div>
  </div>
  <div class="feature" style="top:587px">
    <div class="feature-icon">
      <svg width="50" height="50" viewBox="0 0 50 50" fill="none" stroke="#fff" stroke-width="2.5"><rect x="6" y="6" width="38" height="11" rx="2"/><rect x="6" y="20" width="38" height="11" rx="2"/><rect x="6" y="34" width="38" height="11" rx="2"/><path d="M12 11.5h3M12 25.5h3M12 39.5h3M28 11.5h10M28 25.5h10M28 39.5h10"/></svg>
    </div>
    <div class="feature-body"><h4>EXPERT REMOTE DATA</h4><p>Lorem Ipsum is simply dummy text of the printing and typesetting industry.</p></div>
  </div>
</section>

<section class="services">
  <h2 class="section-title" style="top:77px">Our Services</h2>
  <div class="divider" style="top:137px"></div>

  <article class="service-card" style="left:130px">
    <svg width="76" height="72" viewBox="0 0 76 72" fill="none" stroke="#1160b0" stroke-width="2.5"><rect x="28" y="24" width="20" height="20" fill="#1160b0"/><circle cx="38" cy="8" r="6"/><circle cx="8" cy="34" r="6"/><circle cx="68" cy="34" r="6"/><circle cx="38" cy="63" r="6"/><circle cx="14" cy="60" r="5"/><circle cx="62" cy="60" r="5"/><path d="M38 14v10M14 34h14M48 34h14M38 44v13M28 44l-11 12M48 44l11 12"/></svg>
    <h3>Data Platform<br>Administration</h3>
    <p>It is a long established fact that a reader will be distracted by the readable content of a page when looking at its layout. The point of using Lorem Ipsum</p>
    <a class="btn" href="#">READ MORE</a>
  </article>
  <article class="service-card" style="left:451px">
    <svg width="76" height="72" viewBox="0 0 76 72"><ellipse cx="46" cy="10" rx="22" ry="7" fill="#1160b0"/><path d="M24 14v10c0 4 10 7 22 7s22-3 22-7V14c0 4-10 7-22 7s-22-3-22-7z" fill="#1160b0"/><path d="M24 28v10c0 4 10 7 22 7s22-3 22-7V28c0 4-10 7-22 7s-22-3-22-7z" fill="#1160b0"/><path d="M24 42v10c0 4 10 7 22 7s22-3 22-7V42c0 4-10 7-22 7s-22-3-22-7z" fill="#1160b0"/><circle cx="18" cy="38" r="9" fill="#0e2440"/><path d="M2 70c0-12 7-18 16-18s16 6 16 18z" fill="#0e2440"/></svg>
    <h3>Database<br>Administrators</h3>
    <p>It is a long established fact that a reader will be distracted by the readable content of a page when looking at its layout. The point of using Lorem Ipsum</p>
    <a class="btn" href="#">READ MORE</a>
  </article>
  <article class="service-card" style="left:773px">
    <svg width="76" height="72" viewBox="0 0 76 72" fill="none" stroke="#1160b0" stroke-width="3"><path d="M12 8h40v30H30l-10 9v-9h-8z"/><path d="M56 22h8v28h-7v8l-9-8H30v-8"/><path d="M20 18h24M20 26h18"/></svg>
    <h3>Consulting<br>and Training</h3>
    <p>It is a long established fact that a reader will be distracted by the readable content of a page when looking at its layout. The point of using Lorem Ipsum</p>
    <a class="btn" href="#">READ MORE</a>
  </article>
</section>

<section class="help">
  <h2>How we help you succeed.</h2>
  <p class="lead">It is a long established fact that a reader will be distracted by the readable content of a page when looking.</p>

  <div class="tile" style="left:130px">
    <div class="tile-photo" role="img" aria-label="Team reviewing documents and charts at a desk" style="background:linear-gradient(135deg,#3a3226,#6b5a3c 50%,#2a2822)"></div>
    <div class="tile-shade"></div>
    <h3>EXPERTISE</h3>
    <p>It is a long established fact that a reader will be...</p>
  </div>
  <div class="tile" style="left:453px">
    <div class="tile-photo" role="img" aria-label="Colleagues discussing work around a laptop" style="background:linear-gradient(135deg,#2c3a4c,#5a6472 50%,#2b2d33)"></div>
    <div class="tile-shade"></div>
    <h3>CASE STUDIES</h3>
    <p>It is a long established fact that a reader will be...</p>
  </div>
  <div class="tile" style="left:775px">
    <div class="tile-photo" role="img" aria-label="Hands working on a laptop in a dim office" style="background:linear-gradient(135deg,#23272e,#4a4f58 50%,#1d1f24)"></div>
    <div class="tile-shade"></div>
    <h3>TECHNOLOGIES</h3>
    <p>It is a long established fact that a reader will be...</p>
  </div>
</section>

<section class="blog">
  <h2 class="section-title" style="top:75px">Latest Blog</h2>
  <div class="divider" style="top:135px"></div>

  <article class="post" style="left:170px">
    <div class="post-photo" role="img" aria-label="Rows of servers in a data centre" style="background:linear-gradient(160deg,#0e1f35,#3d5c84 55%,#16263c)"></div>
    <svg class="post-cut" width="257" height="30" viewBox="0 0 257 30"><path d="M0 30L257 2V30z" fill="#fff"/></svg>
    <h4>Lorem Ipsum is simply dummy text of the printing</h4>
    <p>Sed ut perspiciatis unde omnis iste natus error sit voluptatem accusantiu</p>
    <a class="btn" href="#">Read More</a>
    <svg class="post-corner" width="40" height="40"><path d="M0 0L40 40H0z" fill="#1160b0"/></svg>
  </article>
  <article class="post" style="left:470px">
    <div class="post-photo" role="img" aria-label="Server cabinets with cabling" style="background:linear-gradient(160deg,#232a33,#6c7380 55%,#2a3038)"></div>
    <svg class="post-cut" width="257" height="30" viewBox="0 0 257 30"><path d="M0 30L257 2V30z" fill="#fff"/></svg>
    <h4>Lorem Ipsum is simply dummy text of the printing</h4>
    <p>Sed ut perspiciatis unde omnis iste natus error sit voluptatem accusantiu</p>
    <a class="btn" href="#">Read More</a>
    <svg class="post-corner" width="40" height="40"><path d="M0 0L40 40H0z" fill="#1160b0"/></svg>
  </article>
  <article class="post" style="left:770px">
    <div class="post-photo" role="img" aria-label="Brightly lit server room corridor" style="background:linear-gradient(160deg,#2a5b8c,#8fc0e4 55%,#1f4470)"></div>
    <svg class="post-cut" width="257" height="30" viewBox="0 0 257 30"><path d="M0 30L257 2V30z" fill="#fff"/></svg>
    <h4>Lorem Ipsum is simply dummy text of the printing</h4>
    <p>Sed ut perspiciatis unde omnis iste natus error sit voluptatem accusantiu</p>
    <a class="btn" href="#">Read More</a>
    <svg class="post-corner" width="40" height="40"><path d="M0 0L40 40H0z" fill="#1160b0"/></svg>
  </article>
</section>

<section class="testimonial">
  <h3>What Our Clients Say</h3>
  <p class="quote">It is a long established fact that a reader will be distracted by the readable content of a page when looking at its layout. The point of using Lorem Ipsum</p>
  <p class="by">Sed ut perspiciatis unde omnis iste natusiu</p>
  <div class="t-dots"><span></span><span></span><span class="on"></span><span></span></div>
</section>

<section class="cta">
  <div class="cta-panel cta-left">
    <h3>Latest Resources</h3>
    <p>It is a long established fact that a reader will be distracted by the readable content of a page when looking.</p>
    <span class="outline">Read More</span>
  </div>
  <div class="cta-panel cta-right">
    <h3>Work with Us</h3>
    <p>It is a long established fact that a reader will be distracted by the readable content of a page when looking.</p>
    <span class="outline">Contact Us</span>
  </div>
</section>

<footer class="site-footer">
  <div class="footer-brand">KESTROVA</div>

  <div class="footer-col" style="left:509px">
    <h5>CONTACT US</h5>
    <div class="contact-row">
      <svg width="12" height="14" viewBox="0 0 12 14"><path d="M6 0a5 5 0 0 0-5 5c0 4 5 9 5 9s5-5 5-9a5 5 0 0 0-5-5zm0 7a2 2 0 1 1 0-4 2 2 0 0 1 0 4z" fill="#222"/></svg>
      <span>18 Harbor Lane<br>Brenton, OR 97402</span>
    </div>
    <div class="contact-row">
      <svg width="12" height="12" viewBox="0 0 12 12"><path d="M2 0l3 3-1.5 2a7 7 0 0 0 3.5 3.5L9 7l3 3-2 2C5 12 0 7 0 2z" fill="#222"/></svg>
      <span>555.014.2290</span>
    </div>
    <div class="contact-row">
      <svg width="13" height="10" viewBox="0 0 13 10"><rect width="13" height="10" fill="#222"/><path d="M0 0l6.5 5L13 0" stroke="#f1f2f3" fill="none"/></svg>
      <span>info@kestrova.cz</span>
    </div>
  </div>

  <div class="footer-col" style="left:745px">
    <h5>MENU</h5>
    <ul class="menu-list">
      <li>HOME</li><li>ABOUT US</li><li>SOLUTIONS</li><li>TECHNOLOGIES</li><li>BLOG</li><li>CONTACT US</li>
    </ul>
  </div>

  <div class="footer-col" style="left:933px">
    <h5>CONNECT WITH US</h5>
    <div class="connect-row"><span style="background:#2b4f9c"></span>Newsroom</div>
    <div class="connect-row"><span style="background:#1b9ae0"></span>Updates</div>
    <div class="connect-row"><span style="background:#0e2440"></span>Network</div>
  </div>

  <div class="footer-line"></div>
  <p class="copyright">Copyright@2018 All Rights Reserved</p>
</footer>

</body>
</html>
```